W. Darrow Billboard

2 miles ahead on right
Voted number 1 ... again!
California cuisine
Located in Historic Marbury Hill Inn
Picture of a couple dining
www.torvellis.com 555.317.2968

Target Market(s)

travelers

Industry/Entity Type

hospitality

Font styles to use
Serif

Colors
59FF00
82FF00
B8FF75
E3FFCB
F4FFEA
EE7325
F08F49
F5BC92
FAE3D3
FDF4ED

Requirements
Should not have
• bright colors

```html
<!DOCTYPE html>
<html lang="en">
<head>
<meta charset="utf-8">
<title>Torvelli's Billboard</title>
<link rel="stylesheet" href="https://fonts.googleapis.com/css2?family=Playfair+Display:wght@700;900&family=Lilita+One&family=Roboto+Condensed:wght@400;700&family=Oswald:wght@500&display=swap">
<style>
  :root {
    --orange: #e8541c;
    --orange-soft: #ee7325;
    --orange-deep: #c93a12;
    --lime: #8fd41e;
    --lime-dark: #5e9e12;
    --lime-pale: #e3ffcb;
    --paper: #ffffff;
    --grey: #8a8a8a;
    --silver: #d9d9d9;
    --ink: #ffffff;
  }
  * { margin: 0; padding: 0; box-sizing: border-box; }
  html, body { width: 1200px; height: 801px; overflow: hidden; background: var(--paper); }
  .billboard { position: relative; width: 1200px; height: 801px; background: var(--paper); overflow: hidden; }
  .bands { position: absolute; inset: 0; }
  .badge { position: absolute; left: 40px; top: 40px; width: 240px; height: 240px; }
  .badge text { font-family: "Roboto Condensed", sans-serif; }
  .dining-photo {
    position: absolute; left: 30px; top: 300px; width: 470px; height: 330px;
    border-radius: 40px; border: 4px solid var(--orange-soft);
    background: linear-gradient(135deg, #2c4a4a 0%, #5a4a3a 45%, #8a2a2a 80%, #f2eee6 100%);
  }
  .brand { position: absolute; left: 480px; top: 70px; width: 700px; }
  .brand-name {
    font-family: "Playfair Display", serif; font-weight: 900; font-size: 118px;
    color: var(--orange); line-height: 1; letter-spacing: 1px; white-space: nowrap;
  }
  .brand-sub {
    font-family: "Playfair Display", serif; font-weight: 900; color: var(--orange);
    font-size: 30px; letter-spacing: 5px; margin-top: 6px; padding-left: 70px;
  }
  .brand-sub small { display: block; font-size: 20px; letter-spacing: 4px; padding-left: 60px; }
  .tagline {
    position: absolute; right: 40px; top: 300px; white-space: nowrap;
    font-family: "Playfair Display", serif; font-weight: 700; font-size: 34px; color: var(--lime-dark);
  }
  .cuisine {
    position: absolute; right: 30px; top: 375px; white-space: nowrap;
    font-family: "Lilita One", sans-serif; font-size: 74px; line-height: 1; color: var(--lime);
    -webkit-text-stroke: 2px var(--lime-dark);
  }
  .location {
    position: absolute; left: 620px; top: 480px; white-space: nowrap;
    font-family: "Oswald", sans-serif; font-weight: 500; font-size: 40px; line-height: 1.2; color: var(--grey);
  }
  .contact-bar {
    position: absolute; left: 0; right: 0; bottom: 0; height: 140px;
    background: linear-gradient(180deg, var(--orange) 0%, var(--orange-deep) 100%);
    display: flex; align-items: center; justify-content: flex-end; gap: 60px; padding-right: 50px;
    font-family: "Roboto Condensed", sans-serif; font-weight: 700; color: var(--ink); white-space: nowrap;
  }
  .phone { font-size: 58px; }
  .web { font-size: 48px; }
</style>
</head>
<body>
<div class="billboard">
  <svg class="bands" width="1200" height="801" viewBox="0 0 1200 801" aria-hidden="true">
    <polygon points="150,0 250,0 110,660 10,660" fill="var(--orange)"/>
    <polygon points="250,0 320,0 180,660 110,660" fill="var(--lime)"/>
    <path d="M400,190 C700,140 1000,160 1200,240 L1200,300 C1000,220 700,200 400,190 Z" fill="#f1f1f1"/>
  </svg>

  <svg class="badge" viewBox="0 0 240 240" role="img" aria-label="Voted number 1 again badge">
    <circle cx="120" cy="120" r="116" fill="var(--silver)"/>
    <circle cx="120" cy="120" r="104" fill="#f4f4f4"/>
    <circle cx="120" cy="125" r="74" fill="var(--orange-deep)"/>
    <defs><path id="arc" d="M30,120 A90,90 0 0 1 210,120"/></defs>
    <text font-size="26" fill="#444" letter-spacing="3"><textPath href="#arc" startOffset="50%" text-anchor="middle">VOTED NUMBER</textPath></text>
    <text x="120" y="160" font-size="96" font-weight="700" fill="#fff" text-anchor="middle">1</text>
    <text x="120" y="185" font-size="26" font-weight="700" fill="#f2d000" text-anchor="middle" font-style="italic">again!</text>
    <text x="120" y="222" font-size="18" fill="#fff" text-anchor="middle">★ ★ ★ ★ ★</text>
  </svg>

  <div class="dining-photo" role="img" aria-label="Photo of a couple dining at a restaurant table"></div>

  <div class="brand">
    <div class="brand-name">Torvelli's</div>
    <div class="brand-sub">SOUTHWEST<small>BAR &amp; GRILL</small></div>
  </div>
  <div class="tagline">Good Food, Good Life</div>

  <div class="cuisine">California Cuisine</div>
  <div class="location">Historic Marbury Hill Inn</div>

  <div class="contact-bar">
    <span class="phone">555.317.2968</span>
    <span class="web">www.torvellis.com</span>
  </div>
</div>
</body>
</html>
```